Pine Hollow Haven Home Inc. Website Update

We have a couple of broken links such as the "contact us" and would like to add board members and a calendar of events. We are open to a new design.

```html
<!DOCTYPE html>
<html lang="en">
<head>
<meta charset="utf-8">
<title>Pine Hollow Haven Home Inc.</title>
<link href="https://fonts.googleapis.com/css2?family=Cinzel:wght@400;700&family=Open+Sans:wght@400;600;700&display=swap" rel="stylesheet">
<style>
:root{
  --pink:#e2507a;
  --pink-dark:#c63560;
  --pink-light:#f27ea2;
  --ink:#2a2a2a;
  --text:#444;
  --muted:#777;
  --gray:#4a4a4a;
  --dark:#262626;
  --footer:#1f1f1f;
  --blue:#4fa3e3;
  --blue-light:#7cc0f0;
  --white:#fff;
  --line:#dcdcdc;
}
*{box-sizing:border-box;margin:0;padding:0}
html,body{width:1200px;height:4444px;overflow:hidden}
body{position:relative;background:var(--white);font-family:"Open Sans",Arial,sans-serif;color:var(--text)}
.abs{position:absolute}
.emblem{position:absolute;left:50%;transform:translateX(-50%);width:34px;height:34px;border-radius:50%;background:var(--pink);opacity:.85}
.section-title{position:absolute;left:0;width:1200px;text-align:center;font-family:"Cinzel",Georgia,serif;font-weight:700;color:var(--ink);font-size:34px;letter-spacing:1px;line-height:1.15}

/* header */
.site-header{top:0;left:0;width:1200px;height:115px;background:var(--white)}
.nav{position:absolute;top:48px;display:flex;gap:18px;font-size:14px;font-weight:700;color:var(--ink);text-transform:uppercase}
.nav.left{left:155px}.nav.right{left:680px}
.brand{position:absolute;left:520px;top:6px;width:160px;height:160px;border-radius:50%;background:var(--white);border:4px solid var(--pink);display:flex;align-items:center;justify-content:center;text-align:center;z-index:3}
.brand span{font-weight:700;color:var(--pink);font-size:15px;line-height:1.25;padding:0 14px}

/* hero */
.hero{top:115px;left:0;width:1200px;height:660px;overflow:hidden}
.hero-photo{position:absolute;inset:0;background:linear-gradient(120deg,#6b5a52 0%,#a58b7c 40%,#c9b8a8 60%,#7d6a5f 100%)}
.hero-shade{position:absolute;inset:0;background:rgba(30,25,25,.35)}
.hero h1{position:absolute;top:165px;left:160px;width:880px;text-align:center;color:var(--white);font-family:"Cinzel",Georgia,serif;font-weight:400;font-size:40px;line-height:1.25}
.hero h1 strong{display:block;font-weight:700;font-size:44px;white-space:nowrap}
.btn{position:absolute;height:52px;border-radius:26px;display:flex;align-items:center;justify-content:center;font-size:16px;font-weight:600;text-transform:uppercase;color:var(--white)}
.btn-outline{border:3px solid var(--white)}
.btn-pink{background:var(--pink)}
.arrow-btn{position:absolute;top:240px;width:50px;height:50px;border-radius:50%;background:rgba(255,255,255,.35);display:flex;align-items:center;justify-content:center}

/* intro */
.intro-text{position:absolute;top:905px;left:250px;width:700px;text-align:center;font-size:19px;line-height:1.6;color:var(--text)}
.service{position:absolute;width:202px;height:250px;background:var(--white);border:2px solid var(--line);border-radius:6px;box-shadow:0 3px 10px rgba(0,0,0,.12);text-align:center}
.service .icon{width:96px;height:96px;margin:22px auto 10px;border-radius:50%;background:#fbd3df;display:flex;align-items:center;justify-content:center}
.service .icon i{width:72px;height:72px;border-radius:50%;background:var(--pink);display:flex;align-items:center;justify-content:center}
.service h3{font-family:"Cinzel",Georgia,serif;font-weight:700;color:var(--pink);font-size:15px;line-height:1.35;padding:0 18px}

/* events */
.calendar{position:absolute;left:163px;top:1578px;width:380px;height:370px;background:var(--white);border-radius:8px;box-shadow:0 4px 14px rgba(0,0,0,.15);padding:18px 24px}
.cal-head{height:46px;border-radius:23px;background:var(--gray);display:flex;align-items:center;justify-content:space-between;padding:0 8px;color:var(--white);font-family:"Cinzel",Georgia,serif;font-weight:700;font-size:21px}
.cal-head b{width:30px;height:30px;border-radius:50%;border:2px solid #aaa;display:flex;align-items:center;justify-content:center}
.cal-grid{display:grid;grid-template-columns:repeat(7,1fr);margin-top:12px;text-align:center;font-size:17px;color:var(--ink);row-gap:16px}
.cal-grid .dow{font-weight:700;font-size:15px}
.event{position:absolute;left:578px;width:460px;height:120px}
.event .thumb{position:absolute;left:0;top:4px;width:110px;height:110px;border-radius:50%;background:linear-gradient(135deg,#5b3b55,#c98a6f)}
.event h4{position:absolute;left:126px;top:0;color:var(--white);font-size:21px;font-weight:400}
.event p{position:absolute;left:126px;top:34px;width:330px;color:var(--white);font-size:13px;line-height:1.4}
.event a{position:absolute;left:126px;top:84px;color:var(--white);font-size:14px;font-weight:700}

/* board */
.member{position:absolute;top:2218px;width:200px;text-align:center}
.member .portrait{width:200px;height:200px;border-radius:50%;border:4px solid #d6d6d6;background:linear-gradient(160deg,#c9c4bd,#8f8379)}
.member h4{margin-top:26px;font-size:20px;font-weight:600;color:var(--ink)}
.member p{margin:6px auto 0;width:160px;font-size:12.5px;line-height:1.35;color:var(--muted)}
.member .read{margin:22px auto 0;width:140px;height:40px;border:2px solid var(--pink);border-radius:20px;display:flex;align-items:center;justify-content:center;color:var(--pink);font-size:13px;font-weight:600}

/* testimonial */
.quote{position:absolute;top:2822px;left:170px;width:860px;padding:0 70px;text-align:center;color:var(--white);font-size:20px;line-height:1.6}
.quote-mark{position:absolute;font-family:Georgia,serif;font-size:96px;line-height:1;color:var(--white);font-weight:700}
.quote-mark.open{left:0;top:-14px}
.quote-mark.close{right:0;bottom:-62px}
.quote-name{position:absolute;top:2950px;width:1200px;text-align:center;color:var(--white);font-size:24px}
.dots{position:absolute;top:3012px;left:570px;display:flex;gap:8px}
.dots span{width:14px;height:14px;border-radius:50%;border:2px solid var(--white)}
.dots span.on{background:var(--white)}

/* donate / care */
.panel{position:absolute;top:3192px;width:428px;height:282px;border-radius:0 40px 0 40px;text-align:center;color:var(--white);padding:46px 40px 0}
.panel h3{font-family:"Cinzel",Georgia,serif;font-size:32px;font-weight:700;line-height:1}
.panel p{margin-top:14px;font-size:15px;line-height:1.45}
.panel .pill{position:absolute;left:50%;transform:translateX(-50%);bottom:36px;width:166px;height:50px;border:3px solid var(--white);border-radius:25px;display:flex;align-items:center;justify-content:center;font-weight:600;font-size:15px;text-transform:uppercase}
.donate{left:166px;background:linear-gradient(135deg,var(--pink-dark),var(--pink-light))}
.care{left:618px;background:linear-gradient(135deg,var(--blue),var(--blue-light))}

/* contact */
.contact-bg{top:3540px;left:0;width:1200px;height:510px;background:linear-gradient(180deg,#f4f4f4,#d8d8d8);overflow:hidden}
.field{position:absolute;height:48px;background:var(--white);border-radius:3px;box-shadow:0 1px 3px rgba(0,0,0,.1);padding:14px 14px;font-size:16px;color:#666}
.submit{position:absolute;left:518px;top:3925px;width:168px;height:46px;border-radius:23px;background:var(--pink);color:var(--white);display:flex;align-items:center;justify-content:center;font-size:17px;font-weight:600}

/* footer */
.site-footer{top:4045px;left:0;width:1200px;height:330px;background:var(--footer);color:#ddd}
.foot-brand{position:absolute;left:170px;top:70px;width:150px;height:150px;border-radius:50%;border:4px solid var(--pink);background:var(--white);display:flex;align-items:center;justify-content:center;text-align:center}
.foot-brand span{color:var(--pink);font-weight:700;font-size:14px;line-height:1.25;padding:0 12px}
.foot-col h5{font-family:"Cinzel",Georgia,serif;font-weight:700;font-size:17px;color:var(--white);margin-bottom:18px;letter-spacing:.5px}
.foot-col li{list-style:none;font-size:14px;line-height:1.8;color:#ddd}
.contact-line{display:flex;gap:12px;align-items:flex-start;font-size:14px;line-height:1.45;margin-bottom:16px}
.social{display:flex;gap:8px}
.social span{width:30px;height:30px;border-radius:50%;background:#3e7fd6}
.seal{position:absolute;left:912px;top:170px;width:100px;height:100px;border-radius:50%;background:linear-gradient(160deg,#e8c45a,#b48a23)}
.copyright{top:4376px;left:0;width:1200px;height:68px;background:#181818;color:#999;font-size:14px;display:flex;align-items:center;justify-content:center;border-top:1px solid #333}
</style>
</head>
<body>

<header class="abs site-header">
  <nav class="nav left"><span>About</span><span>How you can help</span><span>Services</span></nav>
  <nav class="nav right"><span>Our love of pets</span><span>Contact us</span><span>Haven Walk</span></nav>
  <div class="brand"><span>Pine Hollow Haven Home Inc.</span></div>
</header>

<section class="abs hero">
  <div class="hero-photo" role="img" aria-label="Photo of young women studying together on a living room floor"></div>
  <div class="hero-shade"></div>
  <h1>Welcome to<strong>Pine Hollow Haven Home Inc.</strong></h1>
  <div class="btn btn-outline" style="left:414px;top:292px;width:176px">Our Mission</div>
  <div class="btn btn-pink" style="left:598px;top:292px;width:172px">Our Girls</div>
  <div class="arrow-btn" style="left:80px"><svg width="18" height="18" viewBox="0 0 18 18"><path d="M12 2 5 9l7 7" stroke="#fff" stroke-width="3" fill="none"/></svg></div>
  <div class="arrow-btn" style="left:1070px"><svg width="18" height="18" viewBox="0 0 18 18"><path d="M6 2l7 7-7 7" stroke="#fff" stroke-width="3" fill="none"/></svg></div>
  <svg class="abs" style="left:0;bottom:0" width="1200" height="70" viewBox="0 0 1200 70"><path d="M0 30 Q600 -10 1200 40 L1200 70 0 70Z" fill="var(--pink)"/><path d="M0 42 Q600 2 1200 52 L1200 70 0 70Z" fill="#fff"/></svg>
</section>

<section class="intro">
  <div class="emblem" style="top:780px"></div>
  <h2 class="section-title" style="top:828px">We are Pine Hollow Haven Home</h2>
  <p class="intro-text">With the help of our community, we have raised over 1000 girls and counting! Some of the services we offer include:</p>
  <div class="service" style="left:162px;top:1013px">
    <div class="icon"><i><svg width="38" height="34" viewBox="0 0 38 34"><path d="M3 16 19 3l16 13M8 13v18h22V13" stroke="#fff" stroke-width="3" fill="none"/></svg></i></div>
    <h3>Room, Board, and Watchful Oversight</h3>
  </div>
  <div class="service" style="left:384px;top:1057px">
    <div class="icon"><i><svg width="36" height="32" viewBox="0 0 36 32"><path d="M18 30 4 16a8 8 0 0 1 14-10 8 8 0 0 1 14 10Z" stroke="#fff" stroke-width="3" fill="none"/></svg></i></div>
    <h3>Transitional Living Services</h3>
  </div>
  <div class="service" style="left:606px;top:1013px">
    <div class="icon"><i><svg width="34" height="34" viewBox="0 0 34 34"><circle cx="17" cy="17" r="13" stroke="#fff" stroke-width="3" fill="none"/><path d="M11 17l4 4 8-8" stroke="#fff" stroke-width="3" fill="none"/></svg></i></div>
    <h3>Independent Living Services</h3>
  </div>
  <div class="service" style="left:828px;top:1057px">
    <div class="icon"><i><svg width="36" height="34" viewBox="0 0 36 34"><rect x="4" y="12" width="28" height="19" stroke="#fff" stroke-width="3" fill="none"/><path d="M2 12h32M18 12v19" stroke="#fff" stroke-width="3"/></svg></i></div>
    <h3>Foster Gift Shop</h3>
  </div>
</section>

<section class="events">
  <svg class="abs" style="left:0;top:1370px" width="1200" height="720" viewBox="0 0 1200 720">
    <defs><linearGradient id="evGrad" x1="0" y1="0" x2="0" y2="1"><stop offset="0" stop-color="#d63f6d"/><stop offset="1" stop-color="#f58aab"/></linearGradient></defs>
    <path d="M0 110 Q600 -20 1200 30 L1200 80 Q600 40 0 140Z" fill="var(--gray)"/>
    <path d="M0 130 Q600 30 1200 60 L1200 610 Q700 720 0 690Z" fill="url(#evGrad)"/>
    <path d="M1200 590 Q800 700 0 700 L0 720 1200 720Z" fill="#fff"/>
    <path d="M1200 580 Q900 690 560 705 Q900 700 1200 630Z" fill="var(--gray)"/>
  </svg>
  <div class="emblem" style="top:1446px;background:#fff"></div>
  <h2 class="section-title" style="top:1490px;color:#fff">Event Calendar</h2>
  <div class="calendar">
    <div class="cal-head"><b>‹</b>March 2019<b>›</b></div>
    <div class="cal-grid">
      <span class="dow">MO</span><span class="dow">TU</span><span class="dow">WE</span><span class="dow">TH</span><span class="dow">FR</span><span class="dow">SA</span><span class="dow">SU</span>
      <span>1</span><span>2</span><span>3</span><span>4</span><span>5</span><span>6</span><span>7</span>
      <span>8</span><span>9</span><span>10</span><span>11</span><span>12</span><span>13</span><span>14</span>
      <span>15</span><span>16</span><span>17</span><span>18</span><span>19</span><span>20</span><span>21</span>
      <span>22</span><span>23</span><span>24</span><span>25</span><span>26</span><span>27</span><span>28</span>
      <span>29</span><span>30</span><span>31</span>
    </div>
  </div>
  <div class="event" style="top:1578px">
    <div class="thumb" role="img" aria-label="Event photo"></div>
    <h4>Event Title here</h4>
    <p>Join us for an afternoon of crafts, music and snacks with our girls and their mentors at the home.</p>
    <a>READ MORE</a>
  </div>
  <div class="event" style="top:1712px">
    <div class="thumb" role="img" aria-label="Event photo"></div>
    <h4>Event Title here</h4>
    <p>Volunteers are welcome to help sort donations and prepare gift bags for the coming spring season.</p>
    <a>READ MORE</a>
  </div>
  <div class="event" style="top:1848px">
    <div class="thumb" role="img" aria-label="Event photo"></div>
    <h4>Event Title here</h4>
    <p>Our annual community walk raises support for housing, schooling and life skills for every girl here.</p>
    <a>READ MORE</a>
  </div>
</section>

<section class="board">
  <div class="emblem" style="top:2100px;background:#cfcfcf"></div>
  <h2 class="section-title" style="top:2146px">Board Members</h2>
  <div class="member" style="left:166px"><div class="portrait" role="img" aria-label="Portrait of a board member"></div><h4>Member Name</h4><p>Class aptent taciti sociosqu ad litora torquent</p><div class="read">READ MORE</div></div>
  <div class="member" style="left:386px"><div class="portrait" role="img" aria-label="Portrait of a board member"></div><h4>Member Name</h4><p>Class aptent taciti sociosqu ad litora torquent</p><div class="read">READ MORE</div></div>
  <div class="member" style="left:606px"><div class="portrait" role="img" aria-label="Portrait of a board member"></div><h4>Member Name</h4><p>Class aptent taciti sociosqu ad litora torquent</p><div class="read">READ MORE</div></div>
  <div class="member" style="left:826px"><div class="portrait" role="img" aria-label="Portrait of a board member"></div><h4>Member Name</h4><p>Class aptent taciti sociosqu ad litora torquent</p><div class="read">READ MORE</div></div>
</section>

<section class="testimonial">
  <svg class="abs" style="left:0;top:2630px" width="1200" height="490" viewBox="0 0 1200 490">
    <path d="M0 10 L1200 10 1200 470 Q600 420 0 480Z" fill="var(--dark)" role="img" aria-label="Dimmed photo of a girl writing at a desk"/>
    <path d="M700 10 Q1000 0 1200 60 L1200 10Z" fill="var(--pink)"/>
    <path d="M0 440 Q300 470 620 478 Q300 490 0 490Z" fill="var(--pink)"/>
  </svg>
  <div class="emblem" style="top:2690px;background:#fff"></div>
  <h2 class="section-title" style="top:2750px;color:#fff">What our girls say</h2>
  <blockquote class="quote">
    <span class="quote-mark open">“</span>
    Emotionally heled a lot and I felt supported. I learned how to cook, budget, get a job, buy a car, pay bills, community service and helping others. I would not have gotten here without the Haven Home
    <span class="quote-mark close">”</span>
  </blockquote>
  <div class="quote-name">MARISSA</div>
  <div class="dots"><span></span><span class="on"></span><span></span></div>
</section>

<section class="support">
  <div class="panel donate">
    <h3>Donate</h3>
    <p>We appreciate donations from our community! It is because of the hearts of those around us that we're able to do what we do.</p>
    <div class="pill">Donate Now</div>
  </div>
  <div class="panel care">
    <h3>Care</h3>
    <p>Council for Residential Care Standards certified since 2009<br>To learn more about our CRCS accreditation, please visit www.crcs-standards.org</p>
    <div class="pill">Click Here</div>
  </div>
</section>

<section class="contact">
  <div class="abs contact-bg" role="img" aria-label="Soft grey photo of a person writing at a desk">
    <svg class="abs" style="left:0;top:0" width="1200" height="120" viewBox="0 0 1200 120"><path d="M0 0 H1200 V30 Q700 -10 0 120Z" fill="#fff"/><path d="M0 110 Q600 -10 1200 30 L1200 36 Q600 6 0 120Z" fill="var(--blue)"/></svg>
    <svg class="abs" style="left:0;bottom:0" width="1200" height="60" viewBox="0 0 1200 60"><path d="M0 60 Q600 0 1200 40 L1200 60Z" fill="var(--footer)"/></svg>
  </div>
  <div class="emblem" style="top:3580px"></div>
  <h2 class="section-title" style="top:3628px;color:var(--pink)">Contact Us</h2>
  <div class="field" style="left:192px;top:3686px;width:412px">Your Name</div>
  <div class="field" style="left:608px;top:3686px;width:410px">Phone</div>
  <div class="field" style="left:192px;top:3744px;width:412px">Email</div>
  <div class="field" style="left:608px;top:3744px;width:410px">City</div>
  <div class="field" style="left:192px;top:3808px;width:826px;height:86px">Message</div>
  <div class="submit">Submit</div>
</section>

<footer class="abs site-footer">
  <div class="foot-brand"><span>Pine Hollow Haven Home Inc.</span></div>
  <div class="abs foot-col" style="left:446px;top:66px;width:240px">
    <h5>CONTACT US</h5>
    <div class="contact-line"><svg width="14" height="18" viewBox="0 0 14 18"><path d="M7 17s6-7 6-10A6 6 0 0 0 1 7c0 3 6 10 6 10Z" fill="none" stroke="#ddd" stroke-width="1.6"/><circle cx="7" cy="7" r="2" fill="#ddd"/></svg><span>418 Birchwood Lane, Ellery,<br>GA 30299, USA</span></div>
    <div class="contact-line"><svg width="14" height="14" viewBox="0 0 14 14"><path d="M3 1l2 3-1.5 1.5a8 8 0 0 0 5 5L10 9l3 2-1 2.5C6 13 1 8 .5 2Z" fill="#ddd"/></svg><span>555.014.2287</span></div>
    <div class="contact-line"><svg width="16" height="12" viewBox="0 0 16 12"><rect x="1" y="1" width="14" height="10" fill="none" stroke="#ddd" stroke-width="1.5"/><path d="M1 1l7 6 7-6" fill="none" stroke="#ddd" stroke-width="1.5"/></svg><span>hello@pinehollowhaven.org</span></div>
  </div>
  <div class="abs foot-col" style="left:714px;top:66px">
    <h5>COMPANY</h5>
    <ul><li>About us</li><li>Haven Walk</li><li>Services</li><li>How you can help</li><li>Our Love of Pets</li></ul>
  </div>
  <div class="abs foot-col" style="left:902px;top:66px">
    <h5>GET IN TOUCH</h5>
    <div class="social"><span></span><span></span><span></span><span></span></div>
  </div>
  <div class="seal" role="img" aria-label="Anniversary badge"></div>
</footer>
<div class="abs copyright">Copyright © 2019 All right reserved</div>

</body>
</html>
```